Website design for Silver Harbor Trading Inc

We are looking to build a website for our company. We are a scrap metal recycling company based out of Los Angeles. We purchase scrap metal in the US and ship them to China for recycling into fresh metal ores to supply industrial users. We would designs that emphasize the color green given our name and the nature of our business. Recycling themes are welcomed. We already have a URL at:
http://silverharbortradinginc.example/
At this point, I would like 4 pages:
- Home page
- About Us
- Resources
- Contact us
Our sister company is Maple Crest Intl Inc and they have a website that we can use as a starting point.
http://www.maplecrest-intl.example/
Our competitor has a website below. However we dislike the design given we believe it looks rather dull.
http://www.orientalloysalvage.example/en/
Lastly, this is for a website shell only. Please design the template, graphics, and color schemes. We will write the contents later.

```html
<!DOCTYPE html>
<html lang="en">
<head>
<meta charset="utf-8">
<title>Silver Harbor Trading – Home</title>
<link rel="stylesheet" href="https://fonts.googleapis.com/css2?family=PT+Sans:wght@400;700&family=PT+Sans+Narrow:wght@400;700&family=Source+Sans+3:wght@300;400&display=swap">
<style>
  :root {
    --header-top: #2e8a4c;
    --header-bottom: #135630;
    --white: #ffffff;
    --logo-accent: #9ee0ae;
    --slogan: #c9e8d2;
    --support: #d3ecd9;
    --caption-band: rgba(16, 66, 36, 0.84);
    --caption-sub: #dcefe2;
    --heading-dark: #2b2b2b;
    --body-text: #6a6a6a;
    --service-heading: #1b5a31;
    --service-text: #24502f;
    --bullet: #8cc49c;
    --rule: #e2e2e2;
    --panel-top: #ffffff;
    --panel-bottom: #f0f4f1;
    --panel-border: #dfe4e0;
    --footer-bg: #f4f6f4;
    --footer-text: #333333;
    --social-1: #2f7a45;
    --social-2: #4da868;
    --social-3: #1f5e36;
    --social-4: #7cc18b;
  }
  * { box-sizing: border-box; margin: 0; padding: 0; }
  html, body { width: 1200px; height: 990px; overflow: hidden; background: var(--white); }
  body { position: relative; font-family: "Source Sans 3", sans-serif; }

  .site-header {
    position: absolute; left: 0; top: 0; width: 1200px; height: 383px;
    background: linear-gradient(180deg, var(--header-top) 0%, var(--header-bottom) 100%);
  }
  .brand { position: absolute; left: 104px; top: 40px; display: flex; align-items: center; gap: 12px; }
  .brand-mark { width: 52px; height: 52px; border-radius: 50%; background: var(--logo-accent); }
  .brand-name { font-family: "PT Sans Narrow", sans-serif; font-weight: 700; font-size: 31px; color: var(--white); letter-spacing: 0.3px; line-height: 1; }
  .brand-slogan { position: absolute; left: 174px; top: 81px; font-size: 15px; font-weight: 300; color: var(--slogan); }

  .support { position: absolute; right: 118px; top: 25px; color: var(--support); font-family: "PT Sans", sans-serif; font-size: 13px; }
  .support strong { font-size: 20px; font-weight: 400; color: var(--white); }

  .main-nav { position: absolute; right: 120px; top: 75px; display: flex; }
  .main-nav a { color: var(--white); text-decoration: none; font-family: "PT Sans", sans-serif; font-size: 18.5px; padding: 0 19px; border-left: 1px solid rgba(255,255,255,0.3); line-height: 22px; }
  .main-nav a:first-child { border-left: none; }
  .main-nav a:last-child { padding-right: 0; }

  .hero { position: absolute; left: 96px; top: 126px; width: 700px; height: 387px;
    background: linear-gradient(160deg, #c9ccc8 0%, #8b8b82 30%, #d8e43a 55%, #e86a2a 70%, #c8d83c 100%); }
  .hero-caption { position: absolute; left: -2px; top: 295px; width: 388px; height: 92px; background: var(--caption-band); padding: 14px 0 0 24px; }
  .hero-caption h1 { font-family: "PT Sans Narrow", sans-serif; font-weight: 700; font-size: 37px; color: var(--white); line-height: 40px; }
  .hero-caption p { font-family: "PT Sans Narrow", sans-serif; font-weight: 700; font-size: 13px; color: var(--white); margin-left: 4px; }
  .hero-pager { position: absolute; right: 0; bottom: 0; width: 36px; height: 31px; background: var(--white); display: flex; align-items: center; justify-content: center; }

  .feature-tile { position: absolute; left: 797px; width: 306px; height: 193px; overflow: hidden; }
  .feature-tile.work { top: 126px; background: linear-gradient(180deg, #8fa6bb 0%, #c7d2dc 45%, #7b6e66 100%); }
  .feature-tile.recycling { top: 321px; background: linear-gradient(180deg, #6aa6e0 0%, #9cc3ea 45%, #8c6f62 75%, #4a4640 100%); }
  .feature-caption { position: absolute; left: 0; bottom: 0; width: 100%; height: 57px; background: var(--caption-band); padding: 9px 0 0 22px; }
  .feature-caption h2 { font-family: "PT Sans Narrow", sans-serif; font-weight: 700; font-size: 20px; color: var(--white); line-height: 22px; }
  .feature-caption p { font-size: 12.5px; color: var(--caption-sub); }

  .welcome { position: absolute; left: 109px; top: 550px; width: 672px; }
  .welcome h2 { font-family: "PT Sans Narrow", sans-serif; font-weight: 700; font-size: 24px; color: var(--heading-dark); margin-bottom: 12px; }
  .welcome-photo { float: left; width: 153px; height: 147px; margin: 3px 14px 6px 5px; background: linear-gradient(160deg, #2d58a6 0%, #6b8fc9 45%, #c9d2de 70%, #3a5e9c 100%); }
  .welcome p { font-size: 13.4px; font-weight: 300; line-height: 21.6px; color: var(--body-text); margin-bottom: 5px; }
  .welcome p.full { clear: both; padding-left: 5px; padding-top: 3px; }

  .services { position: absolute; left: 795px; top: 543px; width: 305px; height: 278px;
    background: linear-gradient(180deg, var(--panel-top) 0%, var(--panel-bottom) 100%); border: 1px solid var(--panel-border); padding: 22px 0 0 27px; }
  .services h2 { font-family: "PT Sans Narrow", sans-serif; font-weight: 700; font-size: 23px; color: var(--service-heading); margin-bottom: 8px; }
  .service-list { list-style: none; width: 232px; }
  .service-list li { position: relative; font-size: 13.6px; color: var(--service-text); padding: 6px 0 7px 20px; border-bottom: 1px solid var(--rule); }
  .service-list li:last-child { border-bottom: none; }
  .service-list svg { position: absolute; left: 4px; top: 11px; }

  .site-footer { position: absolute; left: 0; top: 869px; width: 1200px; height: 121px; background: var(--footer-bg); box-shadow: inset 0 4px 6px rgba(0,0,0,0.04); }
  .footer-nav { position: absolute; left: 117px; top: 27px; display: flex; font-size: 17px; color: var(--footer-text); }
  .footer-nav a { color: var(--footer-text); text-decoration: none; }
  .footer-nav span { margin: 0 10px; }
  .copyright { position: absolute; left: 117px; top: 59px; font-size: 13.5px; color: #444; }
  .social { position: absolute; left: 947px; top: 26px; display: flex; gap: 10px; }
  .social a { display: block; width: 27px; height: 27px; border-radius: 2px; }
  .social .s1 { background: var(--social-1); }
  .social .s2 { background: var(--social-2); }
  .social .s3 { background: var(--social-3); }
  .social .s4 { background: var(--social-4); }
</style>
</head>
<body>
  <header class="site-header">
    <div class="brand">
      <span class="brand-mark"></span>
      <span class="brand-name">SILVER HARBOR TRADING</span>
    </div>
    <div class="brand-slogan">Your Slogan goes here</div>
    <div class="support">24/7 Support: <strong>555.014.2287</strong></div>
    <nav class="main-nav">
      <a href="#">Home</a><a href="#">About Us</a><a href="#">Resources</a><a href="#">Contact us</a>
    </nav>
  </header>

  <section class="hero" role="img" aria-label="Photo of workers in hard hats and high-visibility jackets at a scrap metal yard">
    <div class="hero-caption">
      <h1>RECYCLING METALS</h1>
      <p>CLASS APTENT TACITI SOCIOSQU AD LITORA TORQUENT</p>
    </div>
    <div class="hero-pager">
      <svg width="22" height="14" viewBox="0 0 22 14"><path d="M7 2 L2 7 L7 12 M15 2 L20 7 L15 12" fill="none" stroke="#333" stroke-width="1.6"/></svg>
    </div>
  </section>

  <a class="feature-tile work" href="#" role="img" aria-label="Photo of steel framework inside an industrial plant">
    <div class="feature-caption"><h2>HOW WE WORK</h2><p>Donec iaculis diam a nisi accumsan</p></div>
  </a>
  <a class="feature-tile recycling" href="#" role="img" aria-label="Photo of a pile of scrap metal under a blue sky">
    <div class="feature-caption"><h2>METAL RECYCLING</h2><p>Donec iaculis diam a nisi accumsan</p></div>
  </a>

  <main class="welcome">
    <h2>WELCOME TO OUR WEBSITE MAINPAGE</h2>
    <div class="welcome-photo" role="img" aria-label="Photo of a blue steel recycling structure"></div>
    <p>Phasellus felis dolor, scelerisque a, tempus eget, lobortis id, libero. Donec scelerisque leo ac risus. Praesent sit amet est. In dictum, dolor eu dictum porttitor, enim felis viverra mi, eget luctus massa purus quis odio.</p>
    <p>Etiam nulla massa, pharetra facilisis, volutpat in, imperdiet sit amet, sem. Aliquam nec erat at purus cursus interdum. Vestibulum ligula augue, bibendum accumsan, vestibulum ut, commodo a, mi. Morbi ornare gravida elit. Integer congue, augue et malesuada iaculis, ipsum dui aliquet felis, at cursus magna nisl nec elit.</p>
    <p class="full">Phasellus felis dolor, scelerisque a, tempus eget, lobortis id, libero. Donec scelerisque leo ac risus. Praesent sit amet est. In dictum, dolor eu dictum porttitor, enim felis viverra mi, eget luctus massa purus quis odio.</p>
  </main>

  <aside class="services">
    <h2>SERVICES WE PROVIDE</h2>
    <ul class="service-list">
      <li><svg width="6" height="9" viewBox="0 0 6 9"><path d="M0 0 L6 4.5 L0 9 Z" fill="var(--bullet)"/></svg>Aliquam nec erat at purus</li>
      <li><svg width="6" height="9" viewBox="0 0 6 9"><path d="M0 0 L6 4.5 L0 9 Z" fill="var(--bullet)"/></svg>Cursus interdum Vestibulum</li>
      <li><svg width="6" height="9" viewBox="0 0 6 9"><path d="M0 0 L6 4.5 L0 9 Z" fill="var(--bullet)"/></svg>Ligula augue bibendum accumsan</li>
      <li><svg width="6" height="9" viewBox="0 0 6 9"><path d="M0 0 L6 4.5 L0 9 Z" fill="var(--bullet)"/></svg>Vestibulum ut commodo a mi</li>
      <li><svg width="6" height="9" viewBox="0 0 6 9"><path d="M0 0 L6 4.5 L0 9 Z" fill="var(--bullet)"/></svg>Morbi ornare gravida elit.</li>
      <li><svg width="6" height="9" viewBox="0 0 6 9"><path d="M0 0 L6 4.5 L0 9 Z" fill="var(--bullet)"/></svg>Integer congue augue et males</li>
    </ul>
  </aside>

  <footer class="site-footer">
    <nav class="footer-nav">
      <a href="#">Home</a><span>|</span><a href="#">About Us</a><span>|</span><a href="#">Resources</a><span>|</span><a href="#">Contact us</a>
    </nav>
    <p class="copyright">© 2013 Company Name.&nbsp; All right reserved.&nbsp; Term of Use</p>
    <div class="social">
      <a class="s1" href="#" aria-label="Social profile 1"></a>
      <a class="s2" href="#" aria-label="Social profile 2"></a>
      <a class="s3" href="#" aria-label="Social profile 3"></a>
      <a class="s4" href="#" aria-label="News feed"></a>
    </div>
  </footer>
</body>
</html>
```